Q7 Landing Page

We are looking for a creative landing page & a autosignature for our email.
The launchpage will be featuring a dripmeadow provided "widget"
All instructions are in the uploaded ZIP File
**Please note that we require the landing page back complete ready to be uploaded without having to do any modifications**
Reason: Awaiting some further submissions...

```html
<!DOCTYPE html>
<html lang="en">
<head>
<meta charset="utf-8">
<title>Q7-MEDIA Business Card</title>
<link rel="stylesheet" href="https://fonts.googleapis.com/css2?family=Open+Sans:wght@400;600;700&display=swap">
<style>
  :root {
    --ink: #111111;
    --paper: #ffffff;
    --brand-green: #6fb52c;
    --brand-dark: #1c1c1c;
    --link-green: #6aa32a;
    --sky-top: #8fb4d6;
    --sky-mid: #c3d8ea;
    --horizon: #e8eff3;
    --grass-light: #8fbf3a;
    --grass-dark: #3f7a1e;
  }
  html, body {
    margin: 0;
    padding: 0;
    width: 1200px;
    height: 735px;
    overflow: hidden;
    background: var(--paper);
  }
  .card {
    position: relative;
    width: 1200px;
    height: 735px;
    background: var(--paper);
    font-family: "Open Sans", Arial, sans-serif;
    color: var(--ink);
    overflow: hidden;
  }
  .hero-photo {
    position: absolute;
    left: 400px;
    top: 140px;
    width: 800px;
    height: 595px;
    background:
      linear-gradient(to right, var(--paper) 0%, rgba(255,255,255,0.85) 10%, rgba(255,255,255,0) 32%),
      linear-gradient(to bottom, var(--paper) 0%, rgba(255,255,255,0) 22%),
      linear-gradient(to bottom,
        var(--sky-top) 0%,
        var(--sky-mid) 38%,
        var(--horizon) 62%,
        var(--grass-light) 68%,
        var(--grass-dark) 100%);
  }
  .person-name {
    position: absolute;
    left: 54px;
    top: 10px;
    margin: 0;
    font-size: 43px;
    font-weight: 700;
    letter-spacing: 0.5px;
  }
  .person-role {
    position: absolute;
    left: 56px;
    top: 72px;
    margin: 0;
    font-size: 27px;
    font-weight: 400;
  }
  .brand {
    position: absolute;
    left: 50px;
    top: 168px;
    display: flex;
    align-items: center;
    gap: 24px;
  }
  .brand-square {
    width: 108px;
    height: 108px;
    background: var(--brand-green);
  }
  .brand-name {
    margin: 0;
    font-size: 62px;
    font-weight: 700;
    line-height: 1;
    color: var(--brand-dark);
    letter-spacing: 1px;
  }
  .company-name {
    position: absolute;
    left: 50px;
    top: 370px;
    margin: 0;
    font-size: 29px;
    font-weight: 600;
  }
  .contact {
    position: absolute;
    left: 50px;
    top: 410px;
    margin: 0;
    font-size: 19.5px;
    line-height: 27.75px;
    font-style: normal;
  }
  .contact p { margin: 0; }
  .contact .gap { height: 27.75px; }
  .contact a {
    color: var(--link-green);
    text-decoration: underline;
  }
</style>
</head>
<body>
  <main class="card">
    <div class="hero-photo" role="img" aria-label="Photo of a businessman relaxing in a chair with his feet on a desk with a laptop, in a meadow of grass and wildflowers under a blue sky"></div>

    <h1 class="person-name">Dorian Velte</h1>
    <p class="person-role">Founder &amp; Co Ovner</p>

    <div class="brand">
      <div class="brand-square"></div>
      <p class="brand-name">Q7-MEDIA</p>
    </div>

    <h2 class="company-name">Q7-MEDIA(Pty) Ltd</h2>
    <address class="contact">
      <p>Reg. No. 2015/204817/07</p>
      <p>No. 4 Halden Business Park</p>
      <p>Amber Lane, Westvale, 2048</p>
      <p>South Africa</p>
      <div class="gap"></div>
      <p>Phone +27 82 610-4472</p>
      <p>Cell +27 82 610-4472</p>
      <p>Fax +27 11 702-3391</p>
      <p><a href="mailto:dorian.velte@q7-media.com">dorian.velte@q7-media.com</a></p>
      <p><a href="#">www.q7-media.com</a></p>
    </address>
  </main>
</body>
</html>
```